Quillbrookes websites redesign

Www.quill-brookes.com needs to be redesigned along with updations. The incremental material will be provided for the updations. We are looking for complete redesign of the pages with the new content. The complete write up will be provided soon

Target Market(s)

Global

Coding

Coded - Design and coding required

Number of Pages Required

5+ page

Requirements
Must have
• A clean and slick design for the Consulting.
Should not have
• Too many pictures which reduces the speed of the site

```html
<!DOCTYPE html>
<html lang="en">
<head>
<meta charset="utf-8">
<title>Quillbrookes Consultancy</title>
<link href="https://fonts.googleapis.com/css2?family=Lato:wght@300;400;700&family=Noto+Serif:ital@1&display=swap" rel="stylesheet">
<style>
:root{
  --accent:#2a9fd6;
  --navy:#1f2b5e;
  --map:#2f6fc4;
  --text:#444;
  --muted:#777;
  --rule:#d8d8d8;
  --grey-band:#f2f2f2;
  --footer:#1b1b1b;
  --footer-text:#a8a8a8;
  --white:#fff;
}
*{margin:0;padding:0;box-sizing:border-box}
html,body{width:990px;height:1200px;overflow:hidden;background:var(--white)}
body{position:relative;font-family:Arial,Helvetica,sans-serif;color:var(--text)}
.abs{position:absolute}
.heading{font-family:"Lato",Arial,sans-serif}

/* header */
.site-header{left:0;top:0;width:990px;height:52px;background:var(--white)}
.brand{display:flex;align-items:center;gap:7px;font-family:"Lato",sans-serif;font-size:19px;font-weight:400;color:#2c3e63}
.brand-dot{width:18px;height:18px;border-radius:50%;background:#2c3e63}
.site-header .brand{left:223px;top:15px}
.main-nav{right:223px;top:0;display:flex;gap:17px;font-size:8.5px;font-family:"Lato",sans-serif}
.main-nav a{display:block;height:52px;line-height:54px;color:#555;text-decoration:none;position:relative}
.main-nav a.active{color:var(--accent)}
.main-nav a.active::after{content:"";position:absolute;left:-2px;right:-2px;bottom:0;height:2px;background:var(--accent)}

/* hero */
.hero{left:0;top:52px;width:990px;height:269px;background:var(--navy)}
.hero-visual{left:290px;top:22px;width:425px;height:220px;border-radius:40px;
  background:radial-gradient(ellipse at 50% 45%,#3b82d6 0%,#2a64b6 45%,rgba(31,43,94,0) 75%)}
.hero-arrow{top:128px}
.hero-dots{left:479px;top:233px;display:flex;gap:3px}
.hero-dots span{width:6px;height:6px;border-radius:50%;border:1px solid #fff}
.hero-dots span.on{background:#fff}

/* welcome */
.welcome-title{left:0;width:990px;top:375px;text-align:center;font-size:15px;font-weight:300;color:#444;letter-spacing:.3px}
.welcome-title b{font-weight:700}
.short-rule{left:480px;top:410px;width:30px;height:1px;background:#bbb}
.welcome-text{left:320px;top:421px;width:350px;text-align:center;font-size:7.2px;line-height:11px;color:#555}
.btn-outline{left:461px;top:474px;width:68px;height:19px;border:1px solid #c8c8c8;font-size:7px;line-height:18px;text-align:center;color:#555;letter-spacing:.2px}

/* services */
.service{top:528px;width:120px;text-align:center}
.service svg{display:block;margin:0 auto;height:28px}
.service h3{margin-top:15px;font-family:"Lato",sans-serif;font-weight:400;font-size:9px;color:#444;padding-bottom:10px;border-bottom:1px solid var(--rule)}
.service p{margin-top:8px;font-size:6.6px;line-height:12px;color:#777}
.service .more{display:inline-block;margin-top:6px;font-family:"Noto Serif",serif;font-style:italic;font-size:7px;color:#999;padding-bottom:4px}
.service.current h3,.service.current .more{color:var(--accent)}
.service.current .more{border-bottom:1px solid var(--accent)}

/* consultancy */
.band{left:0;top:694px;width:990px;height:290px;background:var(--grey-band)}
.band-title{left:223px;top:733px;width:544px;display:flex;align-items:center;gap:12px;font-family:"Lato",sans-serif;font-size:11px;color:#666;letter-spacing:.3px}
.band-title::before,.band-title::after{content:"";flex:1;height:1px;background:#ddd}
.offer{top:778px;width:172px}
.offer-media{position:relative;height:100px}
.offer-media .go{position:absolute;right:0;bottom:0;width:19px;height:17px;background:#333;display:flex;align-items:center;justify-content:center}
.offer h4{margin-top:14px;font-family:"Lato",sans-serif;font-weight:700;font-size:7.5px;letter-spacing:.4px;color:#444}
.offer p{margin-top:7px;font-size:6.8px;line-height:12px;color:#666}
.offer.current h4{color:var(--accent)}

/* footer */
.site-footer{left:0;top:984px;width:990px;height:216px;background:var(--footer);color:var(--footer-text)}
.site-footer .brand{left:223px;top:38px;color:#999;font-size:14px}
.site-footer .brand-dot{width:15px;height:15px;background:#999}
.f-address{left:224px;top:71px;font-size:6.8px;line-height:12px}
.f-contact{left:224px;top:130px;font-size:7px;line-height:12.5px}
.f-contact b{color:var(--accent)}
.f-contact a{color:var(--accent)}
.f-head{top:42px;font-family:"Lato",sans-serif;font-size:8.5px;color:#eee;letter-spacing:.2px}
.f-head::after{content:"";display:block;width:18px;height:1px;background:#888;margin-top:8px}
.f-note{left:399px;top:72px;font-size:6.8px}
.f-input{left:399px;top:91px;width:123px;height:22px;border:1px solid #555;font-size:6.8px;line-height:21px;padding-left:8px}
.f-input svg{position:absolute;right:6px;top:7px}
.f-links{left:575px;top:70px;list-style:none;font-size:6.8px;line-height:14.8px}
.f-links li::before{content:"»";color:#666;margin-right:6px}
.f-links li.active{color:var(--accent);text-decoration:underline}
.f-social{left:689px;top:73px;display:flex;gap:2px}
.f-social span{width:18px;height:18px;border-radius:50%;border:1.5px solid #ccc}
.f-social span:first-child{border-color:var(--accent)}
.f-rule{left:0;top:186px;width:990px;height:1px;background:#2e2e2e}
.f-copy{left:223px;top:199px;font-size:6.8px;color:#888}
</style>
</head>
<body>

<header class="site-header abs">
  <div class="brand abs"><span class="brand-dot"></span>Quillbrookes</div>
  <nav class="main-nav abs">
    <a class="active">Home</a><a>Founder</a><a>Consultancy</a><a>Platform</a><a>Case Studies</a><a>Contact Us</a>
  </nav>
</header>

<section class="hero abs">
  <div class="hero-visual abs" role="img" aria-label="World map with glowing trade connection lines between continents"></div>
  <svg class="hero-arrow abs" style="left:135px" width="12" height="22" viewBox="0 0 12 22"><path d="M10 1 1 11l9 10" fill="none" stroke="#fff" stroke-width="1.5"/></svg>
  <svg class="hero-arrow abs" style="left:846px" width="12" height="22" viewBox="0 0 12 22"><path d="M2 1l9 10-9 10" fill="none" stroke="#fff" stroke-width="1.5"/></svg>
  <div class="hero-dots abs"><span></span><span class="on"></span><span></span><span></span></div>
</section>

<h1 class="welcome-title abs heading">WELCOME TO <b>QUILLBROOKES</b></h1>
<div class="short-rule abs"></div>
<p class="welcome-text abs">Quillbrookes Consultancy Limited capitalizes on synergies arising from trade and investment linkages between countries and knowledge of traditional and non-traditional pools of liquidity to provide consultancy services to Emerging country banks, Corporates and SMEs.</p>
<div class="btn-outline abs">CONTACT US</div>

<div class="service abs" style="left:221px">
  <svg viewBox="0 0 28 28" width="28"><rect x="2" y="18" width="5" height="9" fill="#888"/><rect x="9" y="14" width="5" height="13" fill="#888"/><rect x="16" y="10" width="5" height="17" fill="#888"/><path d="M2 15 11 8l5 4 9-9" fill="none" stroke="#888" stroke-width="2.2"/><path d="M20 2h6v6z" fill="#888"/></svg>
  <h3>Export Credit Agency</h3>
  <p>Quillbrookes Consultancy Limited (QCL) was exclusively appointed to arrange debt for this project.</p>
  <span class="more">read more</span>
</div>
<div class="service current abs" style="left:362px">
  <svg viewBox="0 0 36 28" width="36"><circle cx="18" cy="8" r="5" fill="var(--accent)"/><circle cx="24" cy="3" r="2.5" fill="var(--accent)"/><path d="M3 17c5-2 9-2 13 0h8c2 0 2 3 0 3h-7 8l7-4c2-1 3 1 2 2l-9 7c-3 2-14 2-22-1z" fill="var(--accent)"/></svg>
  <h3>Regional/Local banks</h3>
  <p>Quillbrookes Consultancy Limited (QCL) was exclusively appointed to arrange debt for this project.</p>
  <span class="more">read more</span>
</div>
<div class="service abs" style="left:503px">
  <svg viewBox="0 0 28 28" width="28"><circle cx="14" cy="14" r="12" fill="#888"/><path d="M14 2v24M2 14h24M5 7h18M5 21h18" stroke="#fff" stroke-width="1.5"/></svg>
  <h3>Structured Financing</h3>
  <p>Quillbrookes Consultancy Limited (QCL) was exclusively appointed to arrange debt for this project.</p>
  <span class="more">read more</span>
</div>
<div class="service abs" style="left:643px">
  <svg viewBox="0 0 28 28" width="28"><path d="M13 3a12 12 0 1 0 12 12H13z" fill="#888"/><path d="M16 1v11h11A11 11 0 0 0 16 1z" fill="#888"/></svg>
  <h3>Bank Lines Business</h3>
  <p>Quillbrookes Consultancy Limited (QCL) was exclusively appointed to arrange debt for this project.</p>
  <span class="more">read more</span>
</div>

<section class="band abs"></section>
<h2 class="band-title abs">CONSULTANCY</h2>

<article class="offer abs" style="left:223px">
  <div class="offer-media" role="img" aria-label="Consultants meeting with clients at a bright office desk" style="background:linear-gradient(135deg,#e9e6e1,#bfb8ae 60%,#8e8478)">
    <span class="go"><svg width="10" height="6" viewBox="0 0 10 6"><path d="M0 3h9M6 0l3 3-3 3" fill="none" stroke="#fff"/></svg></span>
  </div>
  <h4>BANK CONSULTANCY</h4>
  <p>The Consultancy provides access to local/regional banks across Hong Kong, Singapore, Dubai , New York and London</p>
</article>
<article class="offer current abs" style="left:409px">
  <div class="offer-media" role="img" aria-label="Financial report with charts, reading glasses and a pen" style="background:linear-gradient(135deg,#c9a57e,#e7eef6 35%,#b8cde4 70%,#6e85a3)">
    <span class="go" style="background:#fff"><svg width="10" height="6" viewBox="0 0 10 6"><path d="M0 3h9M6 0l3 3-3 3" fill="none" stroke="#333"/></svg></span>
  </div>
  <h4>PLAIN VANILLA FINANCING SOLUTIONS</h4>
  <p>The Consultancy provides access to local/regional banks across Hong Kong, Singapore, Dubai , New York and London</p>
</article>
<article class="offer abs" style="left:595px">
  <div class="offer-media" role="img" aria-label="Keyboard with a solution key beside a blue globe" style="background:linear-gradient(120deg,#dfe6ee,#a9bdd3 50%,#2d5f96 80%,#163e70)">
    <span class="go"><svg width="10" height="6" viewBox="0 0 10 6"><path d="M0 3h9M6 0l3 3-3 3" fill="none" stroke="#fff"/></svg></span>
  </div>
  <h4>STRUCTURED FINANCING SOLUTIONS</h4>
  <p style="color:#888">The Consultancy provides end-to-end structured solutions on the Payables, Receivables or Inventory side for working capital requirements</p>
</article>

<footer class="site-footer abs">
  <div class="brand abs"><span class="brand-dot"></span>Quillbrookes</div>
  <p class="f-address abs">Quillbrookes Consultancy Ltd<br>Suite 04, 9th Floor, Harbourline Tower<br>22 Meridian Road East, Kowloon<br>Hong Kong</p>
  <p class="f-contact abs">T: <b>852-310 57264</b><br>E: <a>hello@quill-brookes.com</a></p>

  <h5 class="f-head abs" style="left:399px">GET IN TOUCH!</h5>
  <p class="f-note abs">Simply Drop Your Mail Here</p>
  <div class="f-input abs">Your Email Here
    <svg width="11" height="7" viewBox="0 0 11 7"><rect width="11" height="7" fill="var(--accent)"/><path d="M0 0l5.5 4L11 0" fill="none" stroke="#1b1b1b" stroke-width=".8"/></svg>
  </div>

  <h5 class="f-head abs" style="left:574px">SITE LINKS</h5>
  <ul class="f-links abs">
    <li class="active">Home</li><li>Founder</li><li>Consultancy</li><li>System</li><li>Case Studies</li><li>Contact</li>
  </ul>

  <h5 class="f-head abs" style="left:689px">SOCIAL LINKS</h5>
  <div class="f-social abs"><span></span><span></span><span></span><span></span></div>

  <div class="f-rule abs"></div>
  <p class="f-copy abs">© 2016. Quillbrookes Consultancy Limited</p>
</footer>

</body>
</html>
```